Lorvex Tilo medical cannibis cultivation company

tag - Tilo rise
Lorvex Tilo medical cannabis cultivation - logo is selected- can we please see bold examples with our selection. We are mainly dealing with medical companies and professionals. We would like to be stand out in the crowd with our designs. Welcome any and all attempts. Thanks

Target Market(s)

Medical and Professional

Industry/Entity Type

Medical And Science

Font styles to use
Sans Serif

Colors

Designer to choose colors to be used in the design.

Requirements
Must have
• Bright colour and be bold- Love the teal and magenta that is currently on the dark background design.
Nice to have
• shading and the 3D affect- The shadowed appearance.
Should not have
• Anything related to illegal activity or un professional manners

```html
<!DOCTYPE html>
<html lang="en">
<head>
<meta charset="utf-8">
<title>Lorvex Tilo — Stationery</title>
<link rel="stylesheet" href="https://fonts.googleapis.com/css2?family=Questrial&display=swap">
<style>
  :root{
    --backdrop:#dcdcdc;
    --paper:#f7f7f7;
    --ink:#444;
    --muted:#666;
    --teal:#1aa6e0;
    --magenta:#9b4aa0;
    --ring:#8a8a8a;
    --night:#000;
  }
  *{box-sizing:border-box;margin:0;padding:0}
  html,body{width:1200px;height:877px;overflow:hidden}
  body{background:var(--backdrop);font-family:"Questrial",sans-serif;color:var(--ink);position:relative}
  .sheet{position:absolute;background:var(--paper);box-shadow:0 1px 3px rgba(0,0,0,.18)}

  /* shared contact list */
  .contact{position:absolute;font-size:8.6px;line-height:10.6px;color:var(--ink);list-style:none}
  .contact li{display:flex;align-items:flex-start;gap:6px}
  .contact svg{width:8px;height:8px;flex:none;margin-top:1px;fill:var(--magenta)}
  .contact .gap{margin-top:3px}

  /* shared name block */
  .brand{position:absolute;text-align:center}
  .brand .ring{display:block;margin:0 auto;border:2px solid var(--ring);border-radius:50%}
  .brand .name{display:block;color:var(--teal);white-space:nowrap;letter-spacing:.5px}
  .brand .tag{display:block;color:var(--ring);text-transform:uppercase;letter-spacing:1.6px;white-space:nowrap}

  /* letterhead */
  .letterhead{left:54px;top:66px;width:527px;height:742px}
  .letterhead .contact{left:48px;top:40px}
  .letterhead .brand{left:375px;top:36px;width:120px}
  .letterhead .ring{width:48px;height:48px}
  .letterhead .name{font-size:16px;line-height:18px;margin-top:9px}
  .letterhead .tag{font-size:6.5px;line-height:8px;margin-top:1px}
  .salutation{position:absolute;left:46px;top:206px;font-size:13.5px;line-height:16px;color:var(--ink)}
  .body{position:absolute;left:46px;top:250px;width:438px;font-size:7.5px;line-height:11.4px;color:var(--muted);text-align:justify}
  .body p{margin-bottom:11.4px}
  .closing{position:absolute;left:46px;top:486px;font-size:8px;line-height:10px;color:var(--muted)}
  .signature{position:absolute;left:42px;top:516px;width:94px;height:40px;background:linear-gradient(90deg,rgba(29,79,160,.18),rgba(29,79,160,.06));border-radius:4px}

  /* business cards */
  .card-front{left:617px;top:110px;width:247px;height:141px;background:#f4f4f4}
  .card-front .name{position:absolute;left:15px;top:11px;font-size:17px;line-height:19px;color:var(--teal);letter-spacing:.4px}
  .card-front .tag{position:absolute;left:15px;top:31px;font-size:6.5px;line-height:8px;color:var(--ring);letter-spacing:1.5px;text-transform:uppercase}
  .card-front .person{position:absolute;left:15px;top:47px;font-size:9.5px;line-height:11px;color:var(--magenta);letter-spacing:.5px;text-transform:uppercase}
  .card-front .role{position:absolute;left:15px;top:60px;font-size:6px;line-height:7px;color:var(--magenta);letter-spacing:.3px;text-transform:uppercase}
  .card-front .contact{left:15px;top:72px;font-size:5.2px;line-height:7.6px}
  .card-front .contact svg{width:5px;height:5px}
  .card-back{left:880px;top:110px;width:248px;height:141px;background:var(--night)}
  .card-back .brand{left:0;right:0;top:28px}
  .card-back .ring{width:62px;height:62px}
  .card-back .name{font-size:18px;line-height:20px;margin-top:6px}
  .card-back .tag{font-size:7px;line-height:9px;margin-top:1px}

  /* envelopes */
  .envelope-back{left:608px;top:299px;width:530px;height:241px;background:#f3f3f3}
  .flap{position:absolute;left:0;top:0;width:530px;height:74px}
  .flap .dot{position:absolute;left:258px;top:22px;width:16px;height:16px;border-radius:50%;border:1.5px solid var(--teal)}
  .envelope-front{left:609px;top:568px;width:530px;height:239px;background:#f5f5f5}
  .envelope-front .brand{left:17px;top:24px;width:120px}
  .envelope-front .ring{width:50px;height:50px}
  .envelope-front .name{font-size:15px;line-height:17px;margin-top:4px}
  .envelope-front .tag{font-size:6.5px;line-height:8px;margin-top:1px}
  .envelope-front .address{position:absolute;left:17px;top:108px;width:120px;text-align:center;font-size:8.3px;line-height:10.6px;color:var(--ink)}
</style>
</head>
<body>

<svg width="0" height="0" style="position:absolute" aria-hidden="true">
  <defs>
    <symbol id="i-pin" viewBox="0 0 10 10"><path d="M5 0a3.5 3.5 0 0 0-3.5 3.5C1.5 6 5 10 5 10s3.5-4 3.5-6.5A3.5 3.5 0 0 0 5 0zm0 5a1.4 1.4 0 1 1 0-2.8A1.4 1.4 0 0 1 5 5z"/></symbol>
    <symbol id="i-phone" viewBox="0 0 10 10"><path d="M2 0l2 2.2-1.1 1.3c.7 1.4 1.8 2.5 3.3 3.3L7.5 5.7 10 7.8 8.7 10C4.2 9.7.3 5.8 0 1.3z"/></symbol>
    <symbol id="i-mobile" viewBox="0 0 10 10"><path d="M2.5 0h5v10h-5zM3.4 1v7h3.2V1z"/></symbol>
    <symbol id="i-fax" viewBox="0 0 10 10"><path d="M2.5 0h5v3h-5zM0 3.6h10V8H8v2H2V8H0zM3 6.5v2.5h4V6.5z"/></symbol>
    <symbol id="i-mail" viewBox="0 0 10 10"><path d="M0 2h10v6H0zM.8 2.6L5 5.6l4.2-3z" fill-rule="evenodd"/></symbol>
    <symbol id="i-web" viewBox="0 0 10 10"><path d="M5 0a5 5 0 1 0 0 10A5 5 0 0 0 5 0zm0 1.2L6.6 3 5.4 4.6 3 4 2.2 2.4A3.8 3.8 0 0 1 5 1.2zm1.5 7.4L6 6.4l2.3-.8.4.6a3.8 3.8 0 0 1-2.2 2.4z"/></symbol>
  </defs>
</svg>

<!-- Letterhead -->
<section class="sheet letterhead">
  <ul class="contact">
    <li><svg><use href="#i-pin"/></svg><span>4210 Fenwick Row<br>Juneau, Alaska 34501</span></li>
    <li class="gap"><svg><use href="#i-phone"/></svg><span>555 201 4478</span></li>
    <li><svg><use href="#i-mobile"/></svg><span>555 730 1926</span></li>
    <li><svg><use href="#i-fax"/></svg><span>555 418 6053</span></li>
    <li><svg><use href="#i-mail"/></svg><span>mara@lorvextilo.com</span></li>
    <li><svg><use href="#i-web"/></svg><span>www.lorvextilo.com</span></li>
  </ul>

  <div class="brand">
    <span class="ring"></span>
    <span class="name">LORVEX TILO</span>
    <span class="tag">Tilo rise</span>
  </div>

  <p class="salutation">Dear Mr. Quillen,</p>

  <div class="body">
    <p>Lorem ipsum dolor sit amet, consectetur adipiscing elit. Donec orci purus, luctus vitae dignissim eu, iaculis sed purus. Vivamus faucibus, ipsum nec aliquet viverra, leo mauris condimentum ligula, sit amet sagittis enim ligula quis arcu. Nam egestas tortor id nisi porttitor mattis. In tortor ante, ultricies in suscipit a, tempus non massa. Vivamus et auctor mi. Fusce vel massa nulla. Phasellus nec eros mauris, et scelerisque orci.</p>
    <p>Donec malesuada orci vitae nulla accumsan porta a id massa. Quisque accumsan iaculis magna sit amet fringilla. Maecenas consequat, magna eget tincidunt semper, odio nibh rutrum mi, id feugiat ante nisi eu risus. Vestibulum nunc orci, rhoncus a placerat in, ultricies in mi. Cras mattis varius eros, vel fringilla nisi suscipit eget. Quisque scelerisque sagittis nulla at porttitor.</p>
    <p>Sed id augue vitae urna euismod commodo aliquet a quam. Pellentesque arcu velit, cursus et malesuada ut, consequat et diam. Nullam erat sem, rhoncus id ullamcorper vitae, rhoncus et arcu. In ultricies ultricies nulla, ut rutrum nisi iaculis at. Donec eu magna a metus ornare faucibus. Fusce aliquet faucibus ultricies. Morbi semper, est id tincidunt gravida, sem arcu adipiscing lacus, ac bibendum nulla leo eu purus. Quisque nec diam sed risus consectetur a cumsan quis quis nibh. Vestibulum id purus lorem.</p>
    <p>It is a long established fact that a reader will be distracted by the readable content of a page when looking at its layout. The point of using Lorem Ipsum is that it has a more-or-less normal distribution of letters, as opposed to using 'Content here, content here', making it look like readable English. Many desktop publishing packages</p>
  </div>

  <p class="closing">Sincerely,</p>
  <div class="signature" role="img" aria-label="Handwritten signature of Mara Quillen in blue ink"></div>
</section>

<!-- Business card, front -->
<section class="sheet card-front">
  <span class="name">LORVEX TILO</span>
  <span class="tag">Tilo rise</span>
  <span class="person">Mara Quillen</span>
  <span class="role">CEO/Founder</span>
  <ul class="contact">
    <li><span>4210 Fenwick Row<br>Juneau, Alaska 34501</span></li>
    <li class="gap"><svg><use href="#i-phone"/></svg><span>555 201 4478</span></li>
    <li><svg><use href="#i-mobile"/></svg><span>555 730 1926</span></li>
    <li><svg><use href="#i-fax"/></svg><span>555 418 6053</span></li>
    <li><svg><use href="#i-mail"/></svg><span>mara@lorvextilo.com</span></li>
    <li><svg><use href="#i-web"/></svg><span>www.lorvextilo.com</span></li>
  </ul>
</section>

<!-- Business card, back -->
<section class="sheet card-back">
  <div class="brand">
    <span class="ring"></span>
    <span class="name">LORVEX TILO</span>
    <span class="tag">Tilo rise</span>
  </div>
</section>

<!-- Envelope, back with flap -->
<section class="sheet envelope-back">
  <svg class="flap" viewBox="0 0 530 74" aria-hidden="true">
    <path d="M0 0H530L522 50Q518 74 494 74H36Q12 74 8 50Z" fill="var(--night)"/>
  </svg>
  <div class="flap"><span class="dot"></span></div>
</section>

<!-- Envelope, front -->
<section class="sheet envelope-front">
  <div class="brand">
    <span class="ring"></span>
    <span class="name">LORVEX TILO</span>
    <span class="tag">Tilo rise</span>
  </div>
  <p class="address">4210 Fenwick Row<br>Juneau, Alaska 34501</p>
</section>

</body>
</html>
```